Lo Mara Menu Design Project

This project is pretty straight forward. You will be given 3 files which include the following:
1. Our proposed menu
2. Our Company logo
3. A sample menu on what we are looking for design wise

Your job is to create a visually pleasing menu that is simple, clean and fresh. Please refer to our home website for additional information. (www.lomara-eats.com) Must be in eps or equivalent format.

Target Market(s)

20s to 40s

Industry/Entity Type

It Company

Requirements
Must have
• Company log
Must be in EPS format

```html
<!DOCTYPE html>
<html lang="en">
<head>
<meta charset="utf-8">
<title>Lo Mara Menu – Dim Sum, Starters, Soup</title>
<link href="https://fonts.googleapis.com/css2?family=Josefin+Sans:ital,wght@0,400;0,600;0,700;1,300;1,400&display=swap" rel="stylesheet">
<style>
  :root {
    --bg-deep: #0c1116;
    --bg-teal: #1d3a40;
    --bg-warm: #4a2a22;
    --accent-red: #c8232c;
    --divider-red: #b0141d;
    --text-light: #f3f1ec;
    --text-soft: #e6e3dc;
    --badge-dark: #050505;
  }
  * { margin: 0; padding: 0; box-sizing: border-box; }
  html, body { width: 1200px; height: 1000px; overflow: hidden; background: var(--bg-deep); }
  .menu {
    position: relative; width: 1200px; height: 1000px; overflow: hidden;
    font-family: "Josefin Sans", sans-serif; color: var(--text-light);
  }
  .menu-backdrop {
    position: absolute; inset: 0;
    background:
      radial-gradient(ellipse 380px 300px at 560px 380px, rgba(120,60,40,.45), transparent 70%),
      radial-gradient(ellipse 500px 380px at 820px 720px, rgba(40,90,95,.55), transparent 70%),
      radial-gradient(ellipse 420px 380px at 180px 250px, rgba(90,50,40,.45), transparent 70%),
      radial-gradient(ellipse 380px 300px at 300px 780px, rgba(35,75,80,.5), transparent 70%),
      linear-gradient(160deg, #15191d 0%, var(--bg-teal) 55%, #101417 100%);
  }
  .menu-divider { position: absolute; left: 600px; top: 0; width: 3px; height: 1000px; background: var(--divider-red); }
  .section-title {
    position: absolute; font-size: 31px; font-weight: 400; letter-spacing: 1px;
    color: var(--accent-red); line-height: 36px; text-transform: uppercase;
  }
  .item-name, .item-price, .price-label {
    position: absolute; font-size: 19px; font-weight: 700; line-height: 25px; white-space: nowrap;
  }
  .item-desc {
    position: absolute; font-size: 19px; font-style: italic; font-weight: 300;
    line-height: 25px; color: var(--text-soft); white-space: nowrap;
  }
  .item-desc.upright { font-style: normal; font-weight: 400; }
  .left .item-name { left: 68px; }
  .left .item-price { left: 470px; }
  .left .item-desc { left: 105px; }
  .right .item-name { left: 645px; }
  .right .item-desc { left: 681px; }
  .brand-mark {
    position: absolute; top: 928px; display: flex; align-items: center; gap: 6px;
    font-size: 14px; font-weight: 700; color: var(--text-light);
  }
  .brand-mark .square { width: 14px; height: 14px; background: var(--accent-red); }
</style>
</head>
<body>
<main class="menu">
  <div class="menu-backdrop" role="img" aria-label="Dim, softly blurred photograph of dumplings and dipping sauce on a dark table"></div>
  <div class="menu-divider"></div>

  <section class="left">
    <h2 class="section-title" style="left:248px; top:24px;">Dim Sum</h2>

    <div class="item-name" style="top:70px;">Pan-Fried Potstickers</div>
    <div class="item-price" style="top:70px;">6.50</div>
    <div class="item-desc" style="top:95px;">Five pan-Fried potstickers with chicken or pork.<br>Served with apricot dipping sauce.</div>

    <div class="item-name" style="top:145px;">Steamed Dumplings</div>
    <div class="item-price" style="top:145px;">6.50</div>
    <div class="item-desc" style="top:170px;">Five steamed dumplings with chicken, or ginger aioli.<br>vegetables. Served with apricot dipping sauce.</div>

    <div class="item-name" style="top:220px;">Szechuan Dumplings</div>
    <div class="item-price" style="top:220px;">6.25</div>
    <div class="item-desc" style="top:245px;">Five chicken dumplings tossed in a spicy cilantro<br>sauce</div>

    <div class="item-name" style="top:295px;">Spring Rolls</div>
    <div class="item-price" style="top:295px; left:472px;">4.50</div>
    <div class="item-desc" style="top:320px;">Two chicken or vegetable spring rolls. Served<br>with apricot dipping sauce.</div>

    <div class="item-name" style="top:370px;">Wonton Stars</div>
    <div class="item-price" style="top:370px;">7.25</div>
    <div class="item-desc" style="top:395px;">Five crispy wonton skins filled with real crab and<br>seasoned cream cheese. Served with sweet and<br>sour dipping sauce.</div>

    <div class="item-name" style="top:470px;">Bao</div>
    <div class="item-price" style="top:470px; left:465px;">5.95</div>
    <div class="item-desc" style="top:510px;">Three fluffy steamed chinese buns filled with<br>barbeque pork.</div>

    <div class="item-name" style="top:585px;">Shrimp Toast</div>
    <div class="item-price" style="top:585px; left:465px;">5.95</div>
    <div class="item-desc" style="top:610px;">Four pieces of fried toast with shrimp, onions,<br>bamboo shoots, and water chestnuts. Served<br>with apricot dipping sauce.</div>

    <div class="item-name" style="top:685px;">Shu Mai</div>
    <div class="item-price" style="top:685px; left:465px;">5.95</div>
    <div class="item-desc upright" style="top:710px;">Six steamed open-Face dumplings with pork,<br>shrimp, and mushrooms.</div>

    <div class="item-name" style="top:760px;">Gift Wrapped Chicken</div>
    <div class="item-price" style="top:760px; left:465px;">5.95</div>
    <div class="item-desc" style="top:785px;">Six chicken breast tenders marinated in soy<br>sauce, sesame oil, and cilantro.</div>

    <div class="item-name" style="top:835px;">Assorted Pleasures</div>
    <div class="item-price" style="top:835px; left:465px;">8.95</div>
    <div class="item-desc" style="top:860px;">Two chicken potstickers, two fried chicken<br>wontons, two gift wrapped chicken, and one<br>vegetable spring roll.</div>
  </section>

  <section class="right">
    <h2 class="section-title" style="left:823px; top:24px;">Starters</h2>

    <div class="item-name" style="top:70px;">Edamame</div>
    <div class="item-price" style="top:70px; left:1078px;">4.00</div>
    <div class="item-desc" style="top:95px;">Steamed Soybean Pods.</div>

    <div class="item-name" style="top:120px;">Lightly Battered Calamari Strips</div>
    <div class="item-price" style="top:120px; left:1077px;">5.95</div>
    <div class="item-desc" style="top:145px;">Six calamari strips, lightly battered with a garlic</div>

    <div class="item-name" style="top:195px;">Lo Mara Crab Cake's</div>
    <div class="item-price" style="top:195px; left:1064px;">11.95</div>
    <div class="item-desc" style="top:220px;">Jumbo lump Maryland crab meat with seasoned<br>with our Lo Mara spice blend. Topped with a<br>kick of spicy aioli.</div>

    <div class="price-label" style="top:295px; left:983px;">Lunch / Dinner</div>
    <div class="item-name" style="top:320px;">Dim Sum And Then Sum</div>
    <div class="item-price" style="top:320px; left:977px;">14.95 / 18.95</div>
    <div class="item-desc" style="top:345px;">Choose three / four half orders: Potstickers,<br>steamed dumplings, szechwan dumplings,<br>spring roll, shrimp toast, chinese chicken salad,<br>hot &amp; sour soup, wonton soup, or mushu, For<br>Shrimp fried rice, beef fried rice, or mushu<br>shrimp, add $1.00.</div>

    <h2 class="section-title" style="left:860px; top:500px;">Soup</h2>
    <div class="price-label" style="top:536px; left:1026px;">SM.&nbsp;&nbsp;&nbsp;LG.</div>

    <div class="item-name" style="top:585px;">Wonton Soup</div>
    <div class="item-price" style="top:585px; left:1013px;">4.95&nbsp;&nbsp;&nbsp;7.50</div>
    <div class="item-desc" style="top:610px;">Chicken or pork wonton dumplings with spinach<br>and scallions in chicken broth.</div>

    <div class="item-name" style="top:660px;">Miso Soup</div>
    <div class="item-price" style="top:660px; left:1013px;">4.95&nbsp;&nbsp;&nbsp;7.50</div>
    <div class="item-desc" style="top:685px;">Miso Based Soup with tofu and scallions</div>

    <div class="item-name" style="top:710px;">Hot And Sour Soup</div>
    <div class="item-price" style="top:710px; left:1013px;">4.95&nbsp;&nbsp;&nbsp;7.50</div>
    <div class="item-desc" style="top:735px;">Shredded pork, scallions, carrots, egg, and soft<br>tofu.</div>

    <div class="item-name" style="top:785px;">Velvet Corn Soup</div>
    <div class="item-price" style="top:785px; left:1085px;">7.25</div>
    <div class="item-desc" style="top:810px;">Cellophane noodles, chicken, sweet corn, green<br>peas, and egg. No modifications</div>
  </section>

  <div class="brand-mark" style="left:16px;"><span class="square"></span><span>Lo Mara</span></div>
  <div class="brand-mark" style="left:1112px;"><span class="square"></span><span>Lo Mara</span></div>
</main>
</body>
</html>
```